Business Card Design

Hi I need a business card designed, we already have the business name logo artwork and would like some concept ideas for the Bus Card layout.
On the back of the card i want to include the products and services that we offer.
We are a Plastics Sheeting manufacture based in Perth Australia.

                                       

We need a BC design for a company called Tarvo Plastics based in Perth Australia.

We supply from DIY to Trade & Industrial  Engineering Markets.

We specialise in:

·         Cut to size panels  (all shapes and sizes)

·         Plastics fabrication & Welding

·         Custom Designs

·         Plastic Repairs

·         PVC Pipe Slotting & PVC Pipe Threading

·         Supplier of all types of engineering plastics and profiles.

Including:           Acrylic / Clarvene

                               Polycarbonate / Dorvil

                               Prismatic Light Diffuser

                               Vantrib

                               HDPE / UHMWPE

                               PVC / PVC Foam

                               Nylon

                               HIPS

```html
<!DOCTYPE html>
<html lang="en">
<head>
<meta charset="utf-8">
<title>Tarvo Plastics – Business Card</title>
<link rel="stylesheet" href="https://fonts.googleapis.com/css2?family=Open+Sans:wght@400;600;700;800&display=swap">
<style>
  :root {
    --page: #e9e9e7;
    --card-white: #ffffff;
    --card-blue: #2a89c4;
    --navy: #1b2f6b;
    --orange: #f0821e;
    --ink: #333a45;
    --bullet-red: #d3222a;
    --white: #ffffff;
    --divider: rgba(255,255,255,0.7);
  }
  * { box-sizing: border-box; margin: 0; padding: 0; }
  html, body {
    width: 1200px; height: 720px; overflow: hidden;
    background: var(--page);
    font-family: "Open Sans", Arial, sans-serif;
  }
  .canvas { position: relative; width: 1200px; height: 720px; }
  .card {
    position: absolute; top: 195px;
    width: 540px; height: 330px;
    border-radius: 4px;
    box-shadow: 0 6px 18px rgba(0,0,0,0.18);
    overflow: hidden;
  }
  /* Front */
  .card--front { left: 40px; background: var(--card-white); }
  .brand {
    position: absolute; left: 36px; top: 34px;
    display: flex; align-items: center; gap: 12px;
  }
  .brand__mark { width: 22px; height: 22px; background: var(--navy); }
  .brand__name {
    font-weight: 800; font-size: 44px; color: var(--navy);
    letter-spacing: -0.5px; line-height: 1;
  }
  .holder { position: absolute; right: 34px; top: 104px; text-align: right; }
  .holder__name { font-weight: 700; font-size: 17px; color: var(--navy); }
  .holder__title { font-size: 13px; color: var(--orange); }
  .contact {
    position: absolute; left: 36px; top: 142px;
    list-style: none; font-size: 13px; color: var(--ink); line-height: 21px;
  }
  .contact__item { display: flex; align-items: center; gap: 7px; }
  .contact__item svg { width: 13px; height: 13px; flex: none; fill: var(--orange); }
  .address {
    position: absolute; left: 36px; top: 236px;
    font-size: 12.5px; color: var(--ink); line-height: 21px;
  }
  .trade {
    position: absolute; left: 36px; top: 290px;
    font-size: 12px; color: var(--ink); line-height: 20px;
  }

  /* Back */
  .card--back { left: 620px; background: var(--card-blue); color: var(--white); }
  .back__brand {
    position: absolute; left: 0; right: 0; top: 22px;
    display: flex; justify-content: center; align-items: center; gap: 12px;
  }
  .back__brand .brand__mark { background: var(--white); }
  .back__brand .brand__name { color: var(--white); font-size: 42px; }
  .offer {
    position: absolute; left: 20px; right: 20px; top: 80px;
    text-align: center; font-weight: 700; font-size: 13px; line-height: 18px;
  }
  .columns {
    position: absolute; left: 26px; right: 16px; top: 128px; bottom: 14px;
    display: flex;
  }
  .col--services { width: 284px; padding-right: 12px; }
  .col--materials {
    flex: 1; padding-left: 16px;
    border-left: 1.5px solid var(--divider);
    margin-top: 6px; align-self: flex-start;
  }
  .col__heading { font-weight: 700; font-size: 17px; margin-bottom: 4px; }
  .list { list-style: none; font-size: 13px; line-height: 19px; }
  .list li { position: relative; padding-left: 13px; }
  .col--materials .list li { white-space: nowrap; }
  .list li::before {
    content: ""; position: absolute; left: 0; top: 7px;
    width: 6px; height: 6px; border-radius: 50%; background: var(--bullet-red);
  }
  .pair { display: inline-block; position: relative; padding-left: 11px; margin-left: 6px; }
  .pair::before {
    content: ""; position: absolute; left: 0; top: 7px;
    width: 6px; height: 6px; border-radius: 50%; background: var(--bullet-red);
  }
</style>
</head>
<body>
<main class="canvas">

  <section class="card card--front" aria-label="Business card front">
    <div class="brand">
      <span class="brand__mark"></span>
      <span class="brand__name">Tarvo Plastics</span>
    </div>

    <div class="holder">
      <p class="holder__name">Your Name</p>
      <p class="holder__title">Title</p>
    </div>

    <ul class="contact">
      <li class="contact__item">
        <svg viewBox="0 0 16 16" aria-hidden="true"><path d="M3.6 1.2l2.3 2.8-1.4 1.7c.9 2 2.6 3.6 4.6 4.6l1.7-1.4 2.8 2.3-1.5 2.5C7.4 13.6 2.4 8.6 1.1 3.4z"/></svg>
        08 9314 5820
      </li>
      <li class="contact__item">
        <svg viewBox="0 0 16 16" aria-hidden="true"><path d="M4.5 0h7a1 1 0 0 1 1 1v14a1 1 0 0 1-1 1h-7a1 1 0 0 1-1-1V1a1 1 0 0 1 1-1zm.8 2v10h5.4V2zm2.7 11a1 1 0 1 0 0 2 1 1 0 0 0 0-2z"/></svg>
        123-000-4567
      </li>
      <li class="contact__item">
        <svg viewBox="0 0 16 16" aria-hidden="true"><path d="M4 1h8v4H4zM1 6h14v7h-3v2H4v-2H1zm4 4v4h6v-4z"/></svg>
        08 9314 5821
      </li>
      <li class="contact__item">
        <svg viewBox="0 0 16 16" aria-hidden="true"><path d="M1 3h14v10H1zm1.5 1.4v.4L8 9l5.5-4.2v-.4z"/></svg>
        sales@tarvoplastics.com.au
      </li>
    </ul>

    <div class="address">
      <p>Unit 4/12 Marlow Circuit Kelvin Park WA 6150</p>
      <p>PO Box 2840 Kelvin Park DC WA 6971</p>
    </div>
    <p class="trade">Kestrel Holdings Pty Ltd T/A Tarvo Plastics ABN: TBA</p>
  </section>

  <section class="card card--back" aria-label="Business card back">
    <div class="back__brand">
      <span class="brand__mark"></span>
      <span class="brand__name">Tarvo Plastics</span>
    </div>

    <p class="offer">The Products And Services That We Offer<br>Are Supplied From Diy To Trade &amp; Industrial Engineering Markets</p>

    <div class="columns">
      <div class="col col--services">
        <h2 class="col__heading">We specialise in:</h2>
        <ul class="list">
          <li>Cut to size panels (all shapes and sizes)</li>
          <li>Plastics fabrication &amp; Welding</li>
          <li>Custom Designs</li>
          <li>Plastic Repairs</li>
          <li>PVC Pipe Slotting &amp; PVC Pipe Threading</li>
          <li>Supplier of all types of engineering plastics and profiles</li>
        </ul>
      </div>
      <div class="col col--materials">
        <h2 class="col__heading">Including:</h2>
        <ul class="list">
          <li>Acrylic / Clarvene</li>
          <li>Polycarbonate / Dorvil</li>
          <li>Prismatic Light Diffuser</li>
          <li>Vantrib <span class="pair">HDPE / UHMWPE</span></li>
          <li>PVC / PVC Foam</li>
          <li>Nylon <span class="pair">HIPS</span></li>
        </ul>
      </div>
    </div>
  </section>

</main>
</body>
</html>
```